Eyecatching website design for commercial lighting business

This contest is all about the graphic design aspect. We need a striking website design for a commercial lighting company. We want something really eye catching to introduce people to our range of induction and LED lights which save businesses money on maintenance and electricity costs.

To be successful in this contest you will need to provide a design and pictures for the pages listed below.

We are using the platform velbrin.com.au and you can see the attached template which everything will be loaded into so we just need HTML files which we can upload and we can do everything else from Velbrin.

The final design should be strong and clean and use the colours and textures in the attached business card file.

Detailed requirements:

Please see attached screenshot of the website template, all we need is a fantastic graphic design and improvement/ incorporation of our logo for the following pages
Page Headings:
1. Home
About Us, Contact Us, snapshot of and link to Blog

Each of the below pages will have several paragraphs of text followed by a list of suitable products which is generated from our product catalogue.

2. Car Park Lighting
3. Educational Lighting
4. Hospitality Lighting
5. Office & Shop Lighting
6. Warehouse Lighting

Some of the website we have seen which are similar in nature are:
http://www.quorvanlamps.com.au/
http://www.tibrox.com/
http://www.gandowlumen.net/commercial-led
but we really want a modern, eye catching and memorable design

Some of the designs built on Velbrin that we like are:

http://www.pemberhollow.com.au/
http://www.marwickgoods.com.au/
http://www.kelmorabay.com.au/

I've also uploaded a couple of photos that we love. We'd like something similar for each industry.

Target Market(s)

Company Owners, Maintenance & Facilities Managers, Electrical Contractors

Industry/Entity Type

Electrical

Coding

Coded - Design and coding required

Number of Pages Required

5+ page

Font styles to use
Sans Serif

Colors
33a6d7
ec1f27

Requirements
Must have
• -Must scale to mobile
• -HTML coded files need to be provided (HTML Bootstrap)
Nice to have
• -Prefer incorporation of our logo into header bar
• -Design of 2-3 advertising banners which can be displayed on the home page
• -Prominent call to action button towards top of page 'Get a quote' or similar
• -Grid based design HTML Bootstrap

```html
<!DOCTYPE html>
<html lang="en">
<head>
<meta charset="utf-8">
<title>Harwell &amp; Pike Business Solutions — Commercial Lighting</title>
<link href="https://fonts.googleapis.com/css2?family=Open+Sans:wght@400;600;700;800&family=Oswald:wght@400;500&display=swap" rel="stylesheet">
<style>
:root{
  --red:#e11d25;
  --red-dark:#a4121a;
  --blue:#33a6d7;
  --navy:#1b3d92;
  --navy-dark:#12296a;
  --ink:#2a2a2a;
  --muted:#6d6d6d;
  --paper:#ffffff;
  --grey:#efefef;
  --line:#dcdcdc;
}
*{margin:0;padding:0;box-sizing:border-box}
html,body{width:1200px;height:2204px;overflow:hidden}
body{font-family:"Open Sans",Arial,sans-serif;color:var(--ink);background:var(--paper);position:relative}
.wrap{position:absolute;left:100px;width:1000px}

/* header */
.site-header{position:absolute;top:0;left:0;width:1200px;height:168px;
  background:linear-gradient(115deg,#3a3a3a 0,#1e1e1e 22%,var(--red-dark) 22.2%,var(--red) 45%,var(--red) 100%)}
.brand{position:absolute;left:100px;top:40px;display:flex;align-items:center;gap:12px}
.brand-mark{width:26px;height:26px;border-radius:50%;background:var(--red)}
.brand-name{font-weight:700;font-size:17px;color:#fff;line-height:1.2;width:160px}
.contact-strip{position:absolute;left:340px;top:46px;color:#fff;font-size:12px;line-height:22px}
.search{position:absolute;left:780px;top:48px;width:320px;height:36px;display:flex}
.search input{flex:1;border:0;background:#fff;padding:0 12px;font:12px "Open Sans",sans-serif;color:#999}
.search button{width:40px;border:0;background:var(--blue);display:flex;align-items:center;justify-content:center}
.main-nav{position:absolute;left:0;top:118px;width:1200px;height:50px;background:rgba(0,0,0,.12);border-top:1px solid rgba(255,255,255,.15)}
.main-nav ul{list-style:none;position:absolute;right:100px;top:0;display:flex;height:50px}
.main-nav li{color:#fff;font-family:Oswald,sans-serif;font-size:16px;text-transform:uppercase;padding:0 28px;line-height:50px;border-left:1px solid rgba(255,255,255,.2)}
.main-nav li:first-child{border-left:0}

/* hero */
.hero{position:absolute;top:168px;left:0;width:1200px;height:512px;
  background:radial-gradient(ellipse at 70% 60%,#2f6a5c 0,#173a3c 30%,#0a1a26 65%,#050a12 100%)}
.hero-caption{position:absolute;left:100px;top:222px}
.hero-caption .line{display:inline-block;background:rgba(0,0,0,.45);color:#fff;font-family:Oswald,sans-serif;font-size:24px;text-transform:uppercase;padding:4px 10px;margin-bottom:6px}
.hero-caption .line.accent{color:#ffd23a}
.btn{display:inline-block;color:#fff;font-size:11px;font-weight:700;text-transform:uppercase;padding:10px 20px}
.btn-red{background:var(--red)}
.btn-blue{background:var(--blue)}
.hero-caption .btn{margin-top:18px}
.hero-arrow{position:absolute;right:40px;top:236px;width:36px;height:36px;background:rgba(0,0,0,.5);display:flex;align-items:center;justify-content:center}

/* welcome */
.welcome{position:absolute;top:680px;left:0;width:1200px;height:360px;background:var(--paper);border-top:4px solid var(--navy)}
.welcome .photo{position:absolute;left:100px;top:50px;width:360px;height:250px;background:linear-gradient(160deg,#f3e2b5,#c9a36a 60%,#7d5a30);box-shadow:0 0 0 6px #fff,0 2px 8px rgba(0,0,0,.25)}
.welcome .text{position:absolute;left:500px;top:50px;width:600px}
h2{font-size:26px;font-weight:800;text-transform:uppercase;color:var(--ink)}
h2 .hl{color:var(--red)}
.welcome p{font-size:13px;line-height:22px;color:var(--muted);margin:16px 0 22px}

/* products */
.products{position:absolute;top:1040px;left:0;width:1200px;height:440px;background:var(--grey)}
.products h2{text-align:center;margin-top:50px}
.rule{width:60px;height:3px;background:var(--red);margin:10px auto 0}
.product-grid{position:absolute;left:100px;top:120px;width:1000px;display:flex;gap:20px}
.product{width:235px;background:#fff;padding:10px;box-shadow:0 1px 3px rgba(0,0,0,.12)}
.product .thumb{height:112px}
.product h3{font-size:14px;font-weight:600;margin:14px 0 8px}
.product p{font-size:11px;line-height:17px;color:var(--muted);margin-bottom:14px}
.product .btn{padding:7px 14px;font-size:10px}

/* media */
.media{position:absolute;top:1480px;left:0;width:1200px;height:420px;background:var(--paper)}
.media h2{font-size:22px;position:absolute;top:50px}
.video{position:absolute;left:100px;top:100px;width:490px;height:290px;background:radial-gradient(ellipse at 40% 40%,#2a4f86,#0d1f40 55%,#050b18)}
.play{position:absolute;left:215px;top:120px;width:60px;height:42px;border-radius:9px;background:var(--red);display:flex;align-items:center;justify-content:center}
.video-bar{position:absolute;left:0;bottom:0;width:100%;height:28px;background:rgba(0,0,0,.6)}
.blog{position:absolute;left:620px;top:100px;width:480px}
.post{display:flex;gap:16px;margin-bottom:24px}
.post .thumb{width:120px;height:120px;flex:none}
.post h4{font-size:13px;font-weight:700;text-transform:uppercase;margin-bottom:6px}
.post .date{font-size:10px;color:var(--muted);margin-bottom:6px}
.post p{font-size:11px;line-height:17px;color:var(--muted)}
.post .more{font-size:11px;color:var(--red);font-weight:600;margin-top:6px}

/* footer */
.site-footer{position:absolute;top:1900px;left:0;width:1200px;height:260px;background:var(--navy);color:#cfd9f3}
.foot-col{position:absolute;top:36px}
.foot-col h5{color:#fff;font-size:12px;font-weight:700;text-transform:uppercase;margin-bottom:12px}
.foot-col li{list-style:none;font-size:11px;line-height:22px}
.field{height:24px;background:#2c4fa6;margin-bottom:6px}
.field-row{display:flex;gap:8px}
.field-row .field{flex:1}
.foot-col .btn{padding:6px 14px;font-size:10px}
.phone{color:#fff;font-size:16px;font-weight:700;margin-bottom:10px}
.socials{display:flex;gap:8px}
.socials span{width:28px;height:28px;border-radius:50%;background:#2c4fa6}
.subscribe{display:flex;height:28px}
.subscribe span{flex:1;background:#fff;font-size:10px;color:#999;padding:6px 8px}
.subscribe b{width:40px;background:var(--blue)}
.foot-bar{position:absolute;top:2160px;left:0;width:1200px;height:44px;background:var(--navy-dark);color:#9fb0db;font-size:10px}
.foot-bar p{position:absolute;left:100px;top:15px}
.foot-bar .dots{position:absolute;right:100px;top:10px;display:flex;gap:8px}
.foot-bar .dots span{width:24px;height:24px;border-radius:50%;background:#2c4fa6}
</style>
</head>
<body>

<header class="site-header">
  <div class="brand"><span class="brand-mark"></span><span class="brand-name">Harwell &amp; Pike Business Solutions</span></div>
  <div class="contact-strip">
    <div>✉ hello@harwellpike.com</div>
    <div>PHONE : (02) 5550 1940</div>
  </div>
  <form class="search">
    <input type="text" value="Search here...">
    <button type="button" aria-label="Search">
      <svg width="16" height="16" viewBox="0 0 16 16"><circle cx="6.5" cy="6.5" r="4.5" fill="none" stroke="#fff" stroke-width="2"/><line x1="10" y1="10" x2="14" y2="14" stroke="#fff" stroke-width="2"/></svg>
    </button>
  </form>
  <nav class="main-nav">
    <ul><li>Home</li><li>About Us</li><li>Products</li><li>Blog</li><li>Contact Us</li></ul>
  </nav>
</header>

<section class="hero" role="img" aria-label="Night photo of floodlit tennis courts with a commercial LED flood light in the foreground">
  <div class="hero-caption">
    <div class="line">Save business money on</div><br>
    <div class="line accent">Maintenance and electricity costs</div><br>
    <span class="btn btn-red">Call to action</span>
  </div>
  <div class="hero-arrow"><svg width="14" height="14" viewBox="0 0 14 14"><path d="M4 2l6 5-6 5" fill="none" stroke="#fff" stroke-width="2"/></svg></div>
</section>

<section class="welcome">
  <div class="photo" role="img" aria-label="Warmly lit interior with ceiling downlights"></div>
  <div class="text">
    <h2>Welcome to <span class="hl">Harwell &amp; Pike Business Solutions</span></h2>
    <p>We supply induction and LED lighting that helps businesses cut their power bills and spend less on upkeep. Our range covers car parks, schools, venues, offices, shops and warehouses, with fittings built to last for years. From first audit to final install, our team helps you choose lights that suit the space, meet the standards and pay for themselves sooner than you expect. Talk to us about a site review and a tailored quote for your building today.</p>
    <span class="btn btn-blue">Read more</span>
  </div>
</section>

<section class="products">
  <h2>Latest <span class="hl">Products</span></h2>
  <div class="rule"></div>
  <div class="product-grid">
    <article class="product">
      <div class="thumb" role="img" aria-label="Car park lit by LED fittings" style="background:linear-gradient(160deg,#5a5a5a,#2b2b2b)"></div>
      <h3>Car Park Lighting</h3>
      <p>Bright, even light for open and covered car parks that cuts running costs.</p>
      <span class="btn btn-blue">Read more</span>
    </article>
    <article class="product">
      <div class="thumb" role="img" aria-label="Classroom with ceiling panels" style="background:linear-gradient(160deg,#e8e4dc,#a9a196)"></div>
      <h3>Educational Lighting</h3>
      <p>Glare-free panels for classrooms and halls that help students stay focused.</p>
      <span class="btn btn-blue">Read more</span>
    </article>
    <article class="product">
      <div class="thumb" role="img" aria-label="Venue with colourful accent lighting" style="background:linear-gradient(160deg,#3b5fd1,#b0307a)"></div>
      <h3>Hospitality Lighting</h3>
      <p>Warm, inviting light for hotels, bars and dining rooms at lower cost.</p>
      <span class="btn btn-blue">Read more</span>
    </article>
    <article class="product">
      <div class="thumb" role="img" aria-label="Open plan office with linear lights" style="background:linear-gradient(160deg,#f0f0f0,#b9bcc2)"></div>
      <h3>Office Lighting</h3>
      <p>Clean, efficient light for offices and shops that lasts for many years.</p>
      <span class="btn btn-blue">Read more</span>
    </article>
  </div>
</section>

<section class="media">
  <h2 style="left:100px">Latest <span class="hl">Video</span></h2>
  <h2 style="left:620px">Our <span class="hl">Blog</span></h2>
  <div class="video" role="img" aria-label="Video still of a street lit by LED lamps at night">
    <div class="play"><svg width="18" height="20" viewBox="0 0 18 20"><path d="M2 1l15 9-15 9z" fill="#fff"/></svg></div>
    <div class="video-bar"></div>
  </div>
  <div class="blog">
    <article class="post">
      <div class="thumb" role="img" aria-label="Office interior with bright lighting" style="background:linear-gradient(160deg,#dfe3e8,#7d8793)"></div>
      <div>
        <h4>Cutting power bills with LED</h4>
        <div class="date">May 22, 2015 &nbsp;·&nbsp; 3 comments</div>
        <p>How one office swapped old tubes for LED panels and halved its lighting costs in the first year of use.</p>
        <div class="more">Read more »</div>
      </div>
    </article>
    <article class="post">
      <div class="thumb" role="img" aria-label="Warehouse with high bay lights" style="background:linear-gradient(160deg,#4a6078,#1d2633)"></div>
      <div>
        <h4>Why induction lights last</h4>
        <div class="date">May 18, 2015 &nbsp;·&nbsp; 5 comments</div>
        <p>Induction lamps run for years with little upkeep, which makes them ideal for tall ceilings and busy sites.</p>
        <div class="more">Read more »</div>
      </div>
    </article>
  </div>
</section>

<footer class="site-footer">
  <div class="foot-col" style="left:100px;width:300px">
    <h5>Contact Us</h5>
    <div class="field-row"><div class="field"></div><div class="field"></div></div>
    <div class="field-row"><div class="field"></div><div class="field"></div></div>
    <div class="field" style="height:40px"></div>
    <span class="btn btn-blue">Submit</span>
  </div>
  <div class="foot-col" style="left:460px">
    <h5>Quick Links</h5>
    <ul><li>› Home</li><li>› About Us</li><li>› Products &amp; Services</li><li>› Blog</li><li>› Contact</li></ul>
  </div>
  <div class="foot-col" style="left:620px">
    <h5>Home</h5>
    <ul><li>› Login</li><li>› Terms &amp; Conditions</li><li>› Privacy Policy</li><li>› Sitemap</li></ul>
  </div>
  <div class="foot-col" style="left:780px">
    <h5>Contact Us</h5>
    <div class="phone">1-800-555-0182</div>
    <div class="socials"><span></span><span></span><span></span></div>
  </div>
  <div class="foot-col" style="left:950px;width:150px">
    <h5>Newsletter</h5>
    <div class="subscribe"><span>Email</span><b></b></div>
  </div>
</footer>
<div class="foot-bar">
  <p>© 2015 Harwell &amp; Pike Business Solutions. All rights reserved.</p>
  <div class="dots"><span></span><span></span></div>
</div>

</body>
</html>
```